Salon and Spa Distributor Business Card

Need a business card. We are are distributor in the salon and spa industry. We identify with natural beauty. Need a card with:
Company Name: Petal Quarry"
Title: "President & CEO"
Address
Company Phone number
email
website
Tag Line:" Natural Care for Every Salon"

Industry/Entity Type

Business

Contact Information for Business Card

Name: Dov Strommen
Title: "President & CEO"
Address: 31 Harlow Ln, Bexmoor, NJ 07813
Company Phone number: 800-463-5918
email: dovstrommen@petalquarry.example
website: www.petalquarry.example

Requirements
Should not have
• No black backgrounds

```html
<!DOCTYPE html>
<html lang="en">
<head>
<meta charset="utf-8">
<title>Petal Quarry – Business Card</title>
<link href="https://fonts.googleapis.com/css2?family=Open+Sans:wght@400;600;700&display=swap" rel="stylesheet">
<style>
  :root {
    --backdrop: #ecebe8;
    --card-white: #ffffff;
    --brand-green: #4e9a44;
    --name-green: #4a9240;
    --text-grey: #6b6b6b;
    --icon-grey: #7a7a7a;
    --rule-grey: #bdbdbd;
    --faint-mark: #f0f0f0;
    --back-light: #5fb74b;
    --back-dark: #086c33;
    --white: #ffffff;
  }
  * { margin: 0; padding: 0; box-sizing: border-box; }
  html, body { width: 1200px; height: 1000px; overflow: hidden; }
  body {
    background: var(--backdrop);
    font-family: "Open Sans", Arial, sans-serif;
    position: relative;
  }
  .card {
    position: absolute;
    left: 266px;
    width: 666px;
    height: 397px;
    overflow: hidden;
    box-shadow: 0 3px 10px rgba(0,0,0,0.18);
  }
  .card--front { top: 74px; background: var(--card-white); }
  .card--back {
    top: 534px;
    background: linear-gradient(90deg, var(--back-light) 0%, #3f9a43 40%, var(--back-dark) 100%);
  }
  .faint-mark {
    position: absolute;
    border-radius: 50%;
  }
  .card--front .faint-mark {
    left: 370px; top: 30px; width: 270px; height: 270px;
    background: var(--faint-mark);
  }
  .card--back .faint-mark {
    left: 40px; top: 40px; width: 240px; height: 240px;
    background: rgba(255,255,255,0.12);
  }
  .brand {
    position: absolute;
    display: flex;
    align-items: center;
    gap: 14px;
    font-weight: 400;
    font-size: 32px;
    letter-spacing: -0.3px;
    white-space: nowrap;
  }
  .brand__dot { width: 44px; height: 44px; border-radius: 50%; }
  .card--front .brand { left: 38px; top: 66px; color: var(--brand-green); }
  .card--front .brand__dot { background: var(--brand-green); }
  .card--back .brand { left: 340px; top: 280px; color: var(--white); }
  .card--back .brand__dot { background: var(--white); }

  .person { position: absolute; left: 32px; top: 188px; }
  .person__name {
    color: var(--name-green);
    font-weight: 700;
    font-size: 22px;
    letter-spacing: 0.4px;
    line-height: 1.1;
  }
  .person__title {
    display: flex; align-items: center; gap: 8px;
    color: var(--text-grey);
    font-size: 15px;
    margin-top: 2px;
  }
  .person__rule {
    width: 195px; height: 2px;
    background: linear-gradient(90deg, var(--rule-grey), rgba(189,189,189,0));
  }
  .contacts { position: absolute; left: 32px; top: 244px; list-style: none; }
  .contacts li {
    display: flex; align-items: center; gap: 7px;
    color: var(--text-grey);
    font-size: 16px;
    height: 24px;
  }
  .contacts svg { width: 14px; height: 14px; fill: var(--icon-grey); }
  .tagline {
    position: absolute; left: 32px; top: 320px;
    color: var(--name-green); font-size: 16px;
  }
  .address {
    position: absolute; left: 32px; top: 345px;
    color: var(--text-grey); font-size: 16px;
  }
</style>
</head>
<body>

<section class="card card--front" aria-label="Card front">
  <div class="faint-mark" aria-hidden="true"></div>
  <div class="brand"><span class="brand__dot"></span>PetalQuarry</div>

  <div class="person">
    <h1 class="person__name">DOV STROMMEN</h1>
    <p class="person__title">President &amp; CEO <span class="person__rule"></span></p>
  </div>

  <ul class="contacts">
    <li>
      <svg viewBox="0 0 16 16" aria-hidden="true"><path d="M2 6c0-2 2.5-3 6-3s6 1 6 3v1h-3V6c0-.6-1.3-1-3-1s-3 .4-3 1v1H2zM4 8h8l2 5H2z"/></svg>
      800-463-5918
    </li>
    <li>
      <svg viewBox="0 0 16 16" aria-hidden="true"><path d="M1 3h14v10H1zM2.5 4.5 8 9l5.5-4.5v-.2h-11z" fill-rule="evenodd"/></svg>
      dovstrommen@petalquarry.example
    </li>
    <li>
      <svg viewBox="0 0 16 16" aria-hidden="true"><path d="M8 1a7 7 0 1 0 0 14A7 7 0 0 0 8 1zm0 2a5 5 0 0 1 4.9 4H10.5C10.3 5.3 9.3 4 8 3zM3.1 7A5 5 0 0 1 7 3.1C6 4.3 5.6 5.6 5.5 7zm0 2h2.4c.1 1.4.6 2.7 1.5 3.9A5 5 0 0 1 3.1 9zm7.4 0h2.4A5 5 0 0 1 9 12.9c.9-1.2 1.4-2.5 1.5-3.9z"/></svg>
      www.petalquarry.example
    </li>
  </ul>

  <p class="tagline">Natural Care for Every Salon</p>
  <p class="address">31 Harlow Ln, Bexmoor, NJ 07813</p>
</section>

<section class="card card--back" aria-label="Card back">
  <div class="faint-mark" aria-hidden="true"></div>
  <div class="brand"><span class="brand__dot"></span>PetalQuarry</div>
</section>

</body>
</html>
```